Design für Geburtskarte A6 hoch, Klappkarte
Zielgruppe
Ich bin Fotograf und habe mich auf Schwangerschafts- und Neugeborenenfotografie spezialisiert. Meine Zielgruppe sind schwangere Frauen im letzten Drittel der Schwangerschaft und frisch gewordene Eltern.
Aufgabenstellung
- sehr schlichtes Design, in der Anlage finden Sie zwei der meist verkauften Karten damit Sie sich vom Stil eine Vorstellung machen können
- Lieferung als offene Indesign 5.5 Datei (so das die Farben, Texte, .... angepasst werden können)
- 2-3 Bilder (querformat) sollen in das Design eingearbeitet werden können
- Die Karten werden von mir nachher als fertig gedruckte Karte an meine Kunden verkauft, dies bitte ich zu berücksichtigen
- ich möchte die Karten so nutzen können das sowohl Geburtskarten für Jungs wie auch für Mädels erstellt werden können
- Format: Din A6 (geschlossen 105x148mm), Klappkarte, hoch, 3mm Beschnitt

```html
<!DOCTYPE html>
<html lang="de">
<head>
<meta charset="utf-8">
<title>Geburtskarte Milo – Klappkarte A6</title>
<link href="https://fonts.googleapis.com/css2?family=Dancing+Script:wght@600&family=Josefin+Sans:wght@300;400&display=swap" rel="stylesheet">
<style>
  :root {
    --backdrop: #e7e3de;
    --paper: #f3f1ee;
    --frame-grey: #d8d7d5;
    --mauve: #a68c84;
    --mauve-soft: #b09a93;
    --white: #ffffff;
    --photo-light: #ebe4dc;
    --photo-mid: #dfcfc2;
    --photo-warm: #d6bba8;
    --photo-deep: #bfa190;
  }
  * { box-sizing: border-box; margin: 0; padding: 0; }
  html, body { width: 1200px; height: 800px; overflow: hidden; }
  body {
    background: var(--backdrop);
    font-family: "Josefin Sans", sans-serif;
    font-weight: 300;
    display: flex;
    align-items: center;
    justify-content: center;
    gap: 56px;
  }

  /* Inside spread: two A6 panels side by side */
  .card-inside {
    position: relative;
    width: 680px;
    height: 480px;
    background: var(--paper);
    box-shadow: 0 6px 18px rgba(90, 70, 55, 0.12);
    display: flex;
  }
  .card-inside::after {
    content: "";
    position: absolute;
    left: 340px; top: 0; bottom: 0;
    width: 1px;
    background: rgba(0, 0, 0, 0.06);
  }
  .spread-photo {
    position: absolute;
    inset: 0;
    background: linear-gradient(120deg, var(--photo-light) 0%, var(--photo-light) 30%, var(--photo-warm) 55%, var(--photo-mid) 80%, var(--photo-light) 100%);
    clip-path: polygon(0 0, 100% 0, 100% 58%, 50% 58%, 50% 42%, 0 37%);
  }
  .panel {
    position: relative;
    width: 340px;
    height: 480px;
  }
  .panel-left .intro {
    position: absolute;
    left: 36px; right: 36px; top: 214px;
  }
  .headline {
    font-family: "Dancing Script", cursive;
    font-weight: 600;
    color: var(--mauve);
    font-size: 46px;
    line-height: 1;
    margin-bottom: 20px;
  }
  .intro-text {
    font-size: 12.5px;
    line-height: 1.55;
    color: var(--mauve-soft);
  }
  .panel-right .body-text {
    position: absolute;
    left: 30px; right: 30px; top: 300px;
    font-size: 12.5px;
    line-height: 1.6;
    color: var(--mauve);
    text-align: center;
  }

  /* Front cover */
  .card-front {
    position: relative;
    width: 340px;
    height: 480px;
    background: var(--frame-grey);
    box-shadow: 0 6px 18px rgba(90, 70, 55, 0.12);
  }
  .cover-photo {
    position: absolute;
    inset: 0;
    background:
      linear-gradient(180deg, rgba(150, 120, 105, 0) 55%, rgba(150, 120, 105, 0.45) 100%),
      radial-gradient(ellipse at 45% 45%, var(--photo-warm) 0%, var(--photo-mid) 45%, var(--photo-light) 80%);
    clip-path: polygon(9% 0, 100% 0, 100% 68%, 72% 100%, 0 100%, 0 7%);
  }
  .cover-name {
    position: absolute;
    left: 0; right: 0; top: 348px;
    text-align: center;
    font-family: "Dancing Script", cursive;
    font-weight: 600;
    font-size: 54px;
    color: var(--white);
    line-height: 1;
  }
  .cover-details {
    position: absolute;
    left: 0; right: 0; top: 418px;
    display: flex;
    justify-content: center;
    align-items: center;
    gap: 8px;
    font-size: 13px;
    font-weight: 400;
    letter-spacing: 0.4px;
    color: var(--white);
    text-shadow: 0 0 6px rgba(110, 85, 72, 0.55);
  }
  .detail-sep {
    width: 3px;
    height: 3px;
    border-radius: 50%;
    background: var(--white);
    box-shadow: 0 0 4px rgba(110, 85, 72, 0.5);
  }
</style>
</head>
<body>
  <section class="card-inside" aria-label="Innenseite der Klappkarte">
    <div class="spread-photo" role="img" aria-label="Querformatiges Foto: schlafendes Neugeborenes in cremefarbener Decke"></div>
    <div class="panel panel-left">
      <div class="intro">
        <h1 class="headline">Milo ist da</h1>
        <p class="intro-text">Hier könnte der Text zu Milo stehen. Igenda sum sent ommo occupta tiorum nons eque inias reperovid maio etuibus. Lorrore suntibus</p>
      </div>
    </div>
    <div class="panel panel-right">
      <p class="body-text">Hier könnte der Text zu Milo stehen. Viducipsant ipsant dolo blanducitas nihilique sequae soluptatus si dolori officat liaspero et asperis electe poribus lum ciumquibus audi blatem. Udi blame num, alitaes aut vel ma aut harit ex earuptios estiorehenem solor audi occae nossum, sentios ipient et, te et doluptatis que conseque prem voluptasi aligeni hillant. Lit etus ever um dollestem. Et mo consed que vernat.</p>
    </div>
  </section>

  <section class="card-front" aria-label="Vorderseite der Klappkarte">
    <div class="cover-photo" role="img" aria-label="Hochformatiges Foto: Neugeborenes liegt auf heller Strickdecke"></div>
    <h2 class="cover-name">Milo</h2>
    <p class="cover-details">
      <span class="detail">49cm</span><span class="detail-sep"></span>
      <span class="detail">3200g</span><span class="detail-sep"></span>
      <span class="detail">12.06.2016</span><span class="detail-sep"></span>
      <span class="detail">6:32</span>
    </p>
  </section>
</body>
</html>
```